New Bicycle shop business card

Hi!
I'm looking for a business card for my new proffesional bike mechanics shop. This shop is only for fixing broken bikes and not selling bikes.
Peferbly a modern and sleek and modern design.
Colors: black, grey, red, white
Information:
Name: Rijwielwerkplaats Vanhoutte
Shop owner: Bart Vanhoutte & Marieke Segers
Website: www.rijwielwerkplaats-vanhoutte.be
Email: info@rijwielwerkplaats-vanhoutte.be
Phone number: +32471902368
Street adres: Kerkweg 46
9940 Bellebeke
Slogan/shop information: Herstellingen van alle merken.
Logo: see files.
Target Market(s)
People who seek a mechanic to fix or upgrade their bikes.
Contact Information for Business Card
Information:
Website: info@rijwielwerkplaats-vanhoutte.be
9940 Bellebeke
Logo: see files.

```html
<!DOCTYPE html>
<html lang="nl">
<head>
<meta charset="utf-8">
<title>Rijwielwerkplaats Vanhoutte – business card</title>
<link rel="stylesheet" href="https://fonts.googleapis.com/css2?family=Open+Sans:wght@400;600;700;800&display=swap">
<style>
  :root {
    --red: #ec1f2d;
    --black: #1a1a1a;
    --grey: #9a9a9a;
    --grey-dark: #8a8a8a;
    --white: #ffffff;
    --backdrop: #d9dadc;
  }
  * { box-sizing: border-box; margin: 0; padding: 0; }
  html, body { width: 1200px; height: 900px; overflow: hidden; }
  body {
    background: var(--backdrop);
    font-family: "Open Sans", Arial, sans-serif;
    position: relative;
  }
  .card {
    position: absolute;
    left: 250px;
    width: 700px;
    height: 400px;
    overflow: hidden;
    box-shadow: 0 6px 18px rgba(0,0,0,.18);
  }

  /* Front */
  .card-front { top: 30px; background: var(--red); }
  .front-brand {
    position: absolute; left: 0; right: 0; top: 140px;
    display: flex; align-items: center; justify-content: center; gap: 14px;
  }
  .brand-square { width: 26px; height: 26px; background: var(--white); flex: none; }
  .front-brand .brand-name {
    font-weight: 800; font-size: 34px; letter-spacing: 1px;
    color: var(--black); text-transform: uppercase; line-height: 1.05;
  }
  .slogan {
    position: absolute; left: 0; right: 0; bottom: 56px;
    text-align: center; color: var(--white); font-size: 15px; letter-spacing: .3px;
  }

  /* Back */
  .card-back { top: 470px; background: var(--white); }
  .side-band { position: absolute; left: 0; top: 0; width: 700px; height: 400px; }
  .corner-tab {
    position: absolute; right: 0; top: 26px; width: 14px; height: 42px; background: var(--red);
  }
  .owners { position: absolute; right: 34px; top: 26px; text-align: right; }
  .owners-label { color: var(--red); font-size: 15px; font-weight: 600; }
  .owners-names { color: var(--grey); font-size: 20px; font-weight: 800; }

  .back-brand {
    position: absolute; right: 34px; top: 120px;
    display: flex; align-items: center; gap: 12px;
  }
  .back-brand .brand-square { background: var(--red); width: 22px; height: 22px; }
  .back-brand .brand-name {
    font-weight: 800; font-size: 24px; color: var(--black);
    text-transform: uppercase; line-height: 1.05; text-align: right;
  }

  .contact { position: absolute; left: 262px; top: 200px; }
  .contact-company { color: var(--red); font-size: 20px; font-weight: 800; }
  .contact-role { color: var(--black); font-size: 14px; font-weight: 600; margin-bottom: 6px; }
  .contact-address { color: var(--grey); font-size: 15px; line-height: 1.3; margin-bottom: 8px; }
  .contact-list { list-style: none; }
  .contact-list li {
    display: flex; align-items: center; gap: 10px;
    color: var(--grey-dark); font-size: 14px; line-height: 1.55;
  }
  .contact-list svg { width: 14px; height: 14px; flex: none; }
</style>
</head>
<body>

<section class="card card-front" aria-label="Card front">
  <div class="front-brand">
    <span class="brand-square" aria-hidden="true"></span>
    <span class="brand-name">Rijwielwerkplaats<br>Vanhoutte</span>
  </div>
  <p class="slogan">Herstellingen van alle merken.</p>
</section>

<section class="card card-back" aria-label="Card back">
  <svg class="side-band" viewBox="0 0 700 400" aria-hidden="true">
    <polygon points="0,0 62,0 255,400 0,400" fill="var(--red)"/>
  </svg>
  <span class="corner-tab" aria-hidden="true"></span>

  <div class="owners">
    <p class="owners-label">Shop owner:</p>
    <p class="owners-names">Bart Vanhoutte &amp; Marieke Segers</p>
  </div>

  <div class="back-brand">
    <span class="brand-square" aria-hidden="true"></span>
    <span class="brand-name">Rijwielwerkplaats<br>Vanhoutte</span>
  </div>

  <div class="contact">
    <p class="contact-company">Rijwielwerkplaats Vanhoutte</p>
    <p class="contact-role">General Manager</p>
    <p class="contact-address">Kerkweg 46<br>9940 Bellebeke</p>
    <ul class="contact-list">
      <li>
        <svg viewBox="0 0 24 24" aria-hidden="true"><path fill="var(--red)" d="M6.6 10.8a15.5 15.5 0 0 0 6.6 6.6l2.2-2.2a1 1 0 0 1 1-.25 11.4 11.4 0 0 0 3.6.57 1 1 0 0 1 1 1V20a1 1 0 0 1-1 1A17 17 0 0 1 3 4a1 1 0 0 1 1-1h3.5a1 1 0 0 1 1 1c0 1.25.2 2.45.57 3.57a1 1 0 0 1-.25 1z"/></svg>
        +32471902368
      </li>
      <li>
        <svg viewBox="0 0 24 24" aria-hidden="true"><rect x="2" y="5" width="20" height="14" rx="1" fill="var(--red)"/><path d="M3 6l9 7 9-7" stroke="#fff" stroke-width="2" fill="none"/></svg>
        info@rijwielwerkplaats-vanhoutte.be
      </li>
      <li>
        <svg viewBox="0 0 24 24" aria-hidden="true"><circle cx="12" cy="12" r="10" fill="var(--red)"/><path d="M2 12h20M12 2c3 3 3 17 0 20M12 2c-3 3-3 17 0 20" stroke="#fff" stroke-width="1.5" fill="none"/></svg>
        www.rijwielwerkplaats-vanhoutte.be
      </li>
    </ul>
  </div>
</section>

</body>
</html>
```